Website design for legal tech start up in Switzerland (B2B)

We are for a legal tech start up in Switzerland called KOVA. We have been running since August 2016. This will be our first live website.

We need a website designed and business card design for our start-up in Switzerland. We also need the Web design to be converted into HTML and CSS files.

Function of website:
• To inform potential customers of our services
• Form a key part of our digital marketing and sales footprint.
• Branding

Please find attached logo.
Updates

Project Deadline Extended Reason: Giving us time to review submissions and provide opportunity for more submissions. Added Thursday, February 16, 2017

Project Deadline Extended
Reason: Looking for more idea's not necessarily set on blue and grey colours only.

Target Market(s)

B2B tech powered legal services.

Industry/Entity Type

Legal

Contact Information for Business Card

Lean and slick design.

Coding

Coded - Design and coding required

Number of Pages Required

5+ page

Requirements
Must have
• VERY LEAN AND CLEAN DESIGN!
• We have received many great standard designs, but we are looking for something more out-of-the box: You can get inspiration from these designs: http://www.pixelvane.com/websites/clean/
• Thanks!!
• Easy content management system
• Well structured coding for additional development
• Responsive webpage for all types of devices
• SEO optimized
• Tabs (Home, services, team, careers, blog, contact us)
• Colour scheme complementary to logo
Nice to have
• Look and Design - Approachable, High-tech, Modern
• Easy to add chat bot capability in future
Should not have
• Too busy/ too much clutter
• Not take to long to load

```html
<!DOCTYPE html>
<html lang="en">
<head>
<meta charset="utf-8">
<title>KOVA — Legal Tech</title>
<link href="https://fonts.googleapis.com/css2?family=Raleway:wght@500;600;700;800&family=Open+Sans:wght@400;600;700&display=swap" rel="stylesheet">
<style>
:root{
  --navy:#1c3664;
  --ink:#333333;
  --heading:#555555;
  --body:#5a5a5a;
  --muted:#efefef;
  --line:#e2e2e2;
  --footer:#444444;
  --footer-dark:#373737;
  --footer-text:#c9c9c9;
  --white:#ffffff;
}
*{margin:0;padding:0;box-sizing:border-box}
html,body{width:674px;height:1200px;overflow:hidden;background:var(--white)}
body{position:relative;font-family:"Open Sans",Arial,sans-serif;color:var(--body)}
a{color:inherit;text-decoration:none}

/* header */
.site-header{position:absolute;left:0;top:0;width:674px;height:48px;background:var(--white)}
.brand{position:absolute;left:90px;top:12px;font-family:"Raleway",sans-serif;font-weight:600;font-size:21px;letter-spacing:1px;color:var(--ink);line-height:24px}
.main-nav a{position:absolute;top:20px;font-family:"Raleway",sans-serif;font-weight:600;font-size:7px;letter-spacing:.3px;color:var(--ink);white-space:nowrap;line-height:9px}
.main-nav a.is-active{color:var(--navy)}
.nav-divider{position:absolute;left:564px;top:18px;width:1px;height:12px;background:#777}
.search-icon{position:absolute;left:575px;top:20px}

/* hero */
.hero{position:absolute;left:0;top:48px;width:674px;height:302px;
  background:linear-gradient(180deg,#1d2a52 0%,#3a3f6a 35%,#6a5a52 62%,#2b2f44 80%,#1a1f30 100%)}
.hero-title{position:absolute;top:122px;width:674px;text-align:center;font-family:"Raleway",sans-serif;font-weight:700;font-size:24px;color:var(--white);letter-spacing:.3px}
.hero-text{position:absolute;top:157px;width:674px;text-align:center;font-family:"Raleway",sans-serif;font-weight:500;font-size:11.6px;line-height:15.5px;color:var(--white)}
.hero-arrow{position:absolute;top:131px;width:27px;height:40px;background:rgba(0,0,0,.35)}
.hero-arrow.prev{left:0}.hero-arrow.next{right:0}

/* features */
.feature{position:absolute;top:388px;width:160px}
.feature svg{position:absolute;left:0;top:2px}
.feature h3{position:absolute;left:47px;top:0;font-family:"Raleway",sans-serif;font-weight:500;font-size:10px;color:var(--ink);white-space:nowrap}
.feature p{position:absolute;left:47px;top:15px;width:115px;font-size:5.9px;line-height:10.4px;color:var(--body)}

/* about */
.about{position:absolute;left:0;top:473px;width:674px;height:262px;background:var(--muted);border-top:1px solid var(--line);border-bottom:1px solid var(--line)}
.about h2{position:absolute;left:93px;top:34px;font-family:"Raleway",sans-serif;font-weight:500;font-size:17px;color:var(--heading)}
.about p{position:absolute;left:90px;top:66px;width:226px;font-size:5.9px;line-height:11.3px;color:var(--body)}
.btn-solid{position:absolute;left:90px;top:189px;width:64px;height:23px;background:var(--navy);color:var(--white);font-size:6.2px;font-weight:700;text-align:center;line-height:23px}
.about-photo{position:absolute;left:330px;top:40px;width:252px;height:172px;
  background:linear-gradient(180deg,#2f7fd6 0%,#8cc5ef 38%,#a9b6bf 52%,#2aa3d6 70%,#0e6fb3 100%)}

/* services */
.services-title{position:absolute;top:767px;width:674px;text-align:center;font-family:"Raleway",sans-serif;font-weight:600;font-size:18px;color:var(--heading)}
.services-intro{position:absolute;left:130px;top:802px;width:414px;text-align:center;font-size:5.9px;line-height:11px;color:var(--body)}
.card{position:absolute;top:842px;width:116px}
.card-photo{width:114px;height:80px}
.card h3{position:absolute;left:0;top:89px;font-family:"Raleway",sans-serif;font-weight:500;font-size:9.8px;color:var(--ink);white-space:nowrap}
.card p{position:absolute;left:0;top:111px;width:116px;font-size:5.9px;line-height:10.4px;color:var(--body)}
.btn-outline{position:absolute;left:0;top:152px;width:54px;height:20px;border:1.2px solid var(--navy);color:var(--navy);font-size:6px;font-weight:700;text-align:center;line-height:18px}

/* footer */
.site-footer{position:absolute;left:0;top:1044px;width:674px;height:124px;background:var(--footer);color:var(--footer-text)}
.footer-brand{position:absolute;left:90px;top:24px;font-family:"Raleway",sans-serif;font-weight:600;font-size:18px;letter-spacing:1px;color:var(--white)}
.footer-about{position:absolute;left:90px;top:52px;width:112px;font-size:5.9px;line-height:10px}
.footer-col{position:absolute;top:26px}
.footer-col h4{font-family:"Open Sans",sans-serif;font-weight:700;font-size:7.3px;color:var(--white);margin-bottom:7px;white-space:nowrap}
.footer-col li{list-style:none;font-size:5.9px;line-height:11.4px;white-space:nowrap}
.contact li{display:flex;align-items:flex-start}
.contact svg{flex:none;margin:2px 5px 0 0}
.bottom-bar{position:absolute;left:0;top:1168px;width:674px;height:32px;background:var(--footer-dark)}
.social{position:absolute;left:92px;top:8px;display:flex;gap:2px}
.social span{position:relative;width:15px;height:15px;border:1.1px solid #e5e5e5;border-radius:50%}
.social span::after{content:"";position:absolute;left:4.4px;top:4.4px;width:4px;height:4px;border-radius:50%;background:#e5e5e5}
.copyright{position:absolute;right:92px;top:12px;font-size:5.7px;color:var(--footer-text)}
</style>
</head>
<body>

<header class="site-header">
  <div class="brand">KOVA</div>
  <nav class="main-nav">
    <a class="is-active" style="left:269px">HOME</a>
    <a style="left:312px">SERVICES</a>
    <a style="left:369px">TEAM</a>
    <a style="left:411px">CAREERS</a>
    <a style="left:466px">BLOG</a>
    <a style="left:508px">CONTACT US</a>
  </nav>
  <span class="nav-divider"></span>
  <svg class="search-icon" width="8" height="8" viewBox="0 0 8 8"><circle cx="3.3" cy="3.3" r="2.4" fill="none" stroke="#333" stroke-width="1.2"/><line x1="5.1" y1="5.1" x2="7.4" y2="7.4" stroke="#333" stroke-width="1.3"/></svg>
</header>

<section class="hero" role="img" aria-label="Night view of a lakeside city with lit historic buildings and a fountain">
  <h1 class="hero-title">WELCOME TO KOVA</h1>
  <p class="hero-text">Lorem ipsum dolor sit amet, consectetur adipiscing elit, sed do eiusmod<br>tem incididunt ut labore et dolore magna al ad minim veniamuis</p>
  <span class="hero-arrow prev"><svg width="27" height="40"><polyline points="16,12 9,20 16,28" fill="none" stroke="#fff" stroke-width="1.2"/></svg></span>
  <span class="hero-arrow next"><svg width="27" height="40"><polyline points="11,12 18,20 11,28" fill="none" stroke="#fff" stroke-width="1.2"/></svg></span>
</section>

<section class="features">
  <div class="feature" style="left:90px">
    <svg width="36" height="38" viewBox="0 0 36 38" fill="none" stroke="#1c3664" stroke-width="1.4"><rect x="1" y="1" width="26" height="32"/><rect x="4" y="4" width="28" height="32" fill="#fff"/><circle cx="18" cy="16" r="6"/><line x1="10" y1="29" x2="26" y2="29"/></svg>
    <h3>Finibunorum</h3>
    <p>Cras mattis consectetur purus tlerm entu lomr ileo risus, porta acco ncur acvestibul mattis consectet umo.</p>
  </div>
  <div class="feature" style="left:258px">
    <svg width="46" height="36" viewBox="0 0 46 36" fill="none" stroke="#1c3664" stroke-width="1.4"><circle cx="14" cy="6" r="4"/><circle cx="23" cy="5" r="4"/><circle cx="32" cy="6" r="4"/><path d="M6 30V16h34v8"/><polyline points="26,28 31,33 44,20"/></svg>
    <h3>Finibunorum</h3>
    <p>Cras mattis consectetur purus tlerm entu lomr ileo risus, porta acco ncur acvestibul mattis consectet umo.</p>
  </div>
  <div class="feature" style="left:432px">
    <svg width="38" height="34" viewBox="0 0 38 34" fill="none" stroke="#1c3664" stroke-width="1.4"><rect x="6" y="2" width="30" height="30"/><line x1="6" y1="10" x2="36" y2="10"/><line x1="6" y1="17" x2="36" y2="17"/><rect x="11" y="22" width="8" height="6"/><rect x="22" y="22" width="10" height="6"/><line x1="1" y1="4" x2="12" y2="30"/></svg>
    <h3>Finibunorum</h3>
    <p>Cras mattis consectetur purus tlerm entu lomr ileo risus, porta acco ncur acvestibul mattis consectet umo.</p>
  </div>
</section>

<section class="about">
  <h2>About Us</h2>
  <p>Sed ut perspiciatis unde omnis iste natus error sit voluptatem accusantium doloremque laudantium, totam rem aperiam, eaque ipsa quae ab illo inventore veritatis et quasi architecto beatae vitae dicta sunt explicabo. Nemo enim ipsam voluptatem quia voluptas sit aspernatur autodit aut fugit, sed quia consequunturmagni dolores eos qui ratione voluptatem sequi nesciuntque porro quisquam est, qui dolorem ipsum quia dolor sit amet, consectetur, adipisci velit, sed quia non numquam eius modi tempora incidunt ut labore et dolore magnam aliquolorem quae rat voluptatem. Ut enim ad minima veniam, quis nostrum exercitationem ullam corporis susciumquam eius modi tempora incidunt ut labore et dolore magnam aliquolorem quaerat voluptatem.</p>
  <a class="btn-solid">READ MORE</a>
  <div class="about-photo" role="img" aria-label="Lakeside house with mountains and clear blue water"></div>
</section>

<section class="services">
  <h2 class="services-title">Legal Startup Company</h2>
  <p class="services-intro">Sed ut perspiciatis unde omnis iste natus error sit voluptatem accusantium doloremque laudantium, totam rem aperiam, eaque ipsa quae ab illo inventore veritatis et quasi architecto beatae vitae dicta sunt explicabo. Nemo enim ipsam voluptatem quia voluptas sit aspernatur aut odit</p>

  <article class="card" style="left:91px">
    <div class="card-photo" role="img" aria-label="People working on laptops in a warm-lit office" style="background:linear-gradient(135deg,#2a2320 0%,#8a5a2c 50%,#d9a24a 100%)"></div>
    <h3>Finibunorum Maloru</h3>
    <p>Cras mattis consectetur purus sitlerm entu lomr ileo risus, porta acco nsecur acvestibul mattis consectet umo.</p>
    <a class="btn-outline">READ MORE</a>
  </article>
  <article class="card" style="left:217px">
    <div class="card-photo" role="img" aria-label="Team gathered around a laptop" style="background:linear-gradient(135deg,#b9a08a 0%,#6b5446 55%,#d8d2c8 100%)"></div>
    <h3>Finibunorum Maloru</h3>
    <p>Cras mattis consectetur purus sitlerm entu lomr ileo risus, porta acco nsecur acvestibul mattis consectet umo.</p>
    <a class="btn-outline">READ MORE</a>
  </article>
  <article class="card" style="left:343px">
    <div class="card-photo" role="img" aria-label="Planning sketches and sticky notes on a table" style="background:linear-gradient(135deg,#5d5753 0%,#bdb3a8 50%,#e6c9b6 100%)"></div>
    <h3>Finibunorum Maloru</h3>
    <p>Cras mattis consectetur purus sitlerm entu lomr ileo risus, porta acco nsecur acvestibul mattis consectet umo.</p>
    <a class="btn-outline">READ MORE</a>
  </article>
  <article class="card" style="left:469px">
    <div class="card-photo" role="img" aria-label="Hand sketching an idea diagram on paper" style="background:linear-gradient(135deg,#eef0f3 0%,#d3d8df 60%,#9aa3b2 100%)"></div>
    <h3>Finibunorum Maloru</h3>
    <p>Cras mattis consectetur purus sitlerm entu lomr ileo risus, porta acco nsecur acvestibul mattis consectet umo.</p>
    <a class="btn-outline">READ MORE</a>
  </article>
</section>

<footer class="site-footer">
  <div class="footer-brand">KOVA</div>
  <p class="footer-about">Sed ut perspiciatis unde omnis iste natus error sit voluptatem accusa ntium doloueotam rem aperiam ea que ipsauae aomnis iste natuil.</p>

  <div class="footer-col" style="left:216px">
    <h4>ABOUT US</h4>
    <ul><li>About Us</li><li>Careers</li><li>Leadership</li><li>Locations</li><li>Resources</li></ul>
  </div>
  <div class="footer-col" style="left:294px">
    <h4>SUPPORT</h4>
    <ul><li>Customer Love</li><li>Venture Capital</li><li>Corporate Venture Capital</li><li>Innovation</li><li>Corporate Strategy</li></ul>
  </div>
  <div class="footer-col" style="left:397px">
    <h4>OTHER</h4>
    <ul><li>Pricing</li><li>Privacy Policy</li><li>Terms of Service</li><li>Editor</li></ul>
  </div>
  <div class="footer-col contact" style="left:487px">
    <h4>GET IN TOUCH</h4>
    <ul>
      <li><svg width="5" height="6" viewBox="0 0 5 6"><path d="M2.5 6 0.6 3A2 2 0 1 1 4.4 3Z" fill="#ddd"/></svg><span>Postal address: PO Box 5 lorem<br>Cobar dummy adre dummy</span></li>
      <li><svg width="5" height="6" viewBox="0 0 5 6"><path d="M1 0.5 2 0.3 2.6 1.8 1.9 2.4Q2.5 3.6 3.4 4.1L4 3.4 5 4 4.8 5Q2 5.2 0.6 1.5Z" fill="#ddd"/></svg><span>Phone: 908-555-0142</span></li>
      <li><svg width="5" height="6" viewBox="0 0 5 6"><rect x="0" y="1.3" width="5" height="3.6" fill="#ddd"/><polyline points="0,1.3 2.5,3.3 5,1.3" fill="none" stroke="#444" stroke-width=".5"/></svg><span>hello@kovalegal.ch</span></li>
    </ul>
  </div>
</footer>

<div class="bottom-bar">
  <div class="social" aria-label="Social links"><span></span><span></span><span></span><span></span></div>
  <p class="copyright">© 2017 Kova. All Copyrights are reserved. Privacy Policy</p>
</div>

</body>
</html>
```